Sleek Design For Personal Brand Wordpress Website !!

*WORDPRESS WEBSITE*

Need a sleek and easy to navigate Wordpress website.

It will act as the hub for my personal brand.

Which means it will showcase all my social media outlets, host my most recent content like youtube videos and podcasts...

It will also be the go to place to find all my digital products and services that I offer.

i want it to be super sleek and simple but also give a personal touch of my who I really am. You can get a good idea of who I am my checking out my Instagram (@karim.dulvane)

Use these websites for ideas: www.bronvikel.com and www.teodorplaskewicz.com

Target Market(s)

Young Entrepreneurs

Industry/Entity Type

Education

Logo Text

Karim Dulvane

Number of Pages Required

4 page

Font styles to use
Sans Serif

Colors
ffffff
0392cd
ec1f27

Requirements
Must have
• Social Media buttons on the home page...
• Video (also a slider) right at the top of the home page...
• Email Optin...
• Multiple pages...

```html
<!DOCTYPE html>
<html lang="en">
<head>
<meta charset="utf-8">
<title>Karim Dulvane</title>
<link href="https://fonts.googleapis.com/css2?family=Roboto:ital,wght@0,300;0,400;0,500;0,700;1,700&display=swap" rel="stylesheet">
<style>
:root{
  --red:#e7151f;
  --black:#000;
  --ink:#111;
  --muted:#7a7a7a;
  --panel:#ececec;
  --field-line:#b9b9b9;
  --footer:#1e1e1e;
  --pagebook:#3b5998;
  --chirper:#2aa9e0;
  --circlely:#dd4b39;
  --workline:#1a84bc;
  --pinboardy:#c4303a;
}
*{box-sizing:border-box;margin:0;padding:0}
html,body{width:677px;height:1200px;overflow:hidden;background:#fff}
body{position:relative;font-family:'Roboto',sans-serif;color:var(--ink)}
.abs{position:absolute}
.sidebar{left:0;top:0;width:35px;height:1200px;background:var(--black)}
.menu-icon{left:9px;top:33px;width:17px}
.menu-icon span{display:block;height:2px;background:#fff;margin-bottom:4px}
.brand{display:flex;align-items:center;gap:6px}
.brand-dot{width:10px;height:10px;border-radius:50%;background:var(--red)}
.brand-name{font-weight:700;font-size:17px;line-height:1;color:var(--red);letter-spacing:.3px}
.footer .brand-name{color:#fff}
.social-sq{width:25px;height:25px;border:1px solid #ccc;display:flex;align-items:center;justify-content:center;font-size:9px;color:#aaa}
.hero-panel{left:36px;top:110px;width:453px;height:235px;background:linear-gradient(100deg,#f1f1f1,#d9d9d9 70%,#c9c9c9)}
.hero-video{left:349px;top:84px;width:267px;height:185px;background:linear-gradient(135deg,#7d6e5c,#a48e76 50%,#5b5047)}
.play{left:460px;top:154px;width:44px;height:44px}
.hero-title{left:91px;top:124px;font-size:46px;font-weight:700;line-height:47px;color:var(--black)}
.hero-rule{left:91px;top:224px;width:181px;height:1px;background:#222}
.hero-sub{left:92px;top:240px;font-size:12.5px;font-weight:300;line-height:15.5px;color:#222}
.btn-red{background:var(--red);color:#fff;font-weight:500;display:flex;align-items:center;justify-content:center}
.hero-btn{left:92px;top:292px;width:206px;height:34px;font-size:12px}
.arrow{width:33px;height:38px;background:var(--black);display:flex;align-items:center;justify-content:center}
.card-img{background:linear-gradient(135deg,#8b7a66,#b29a82 55%,#6b5e52)}
.card-img.small-a{background:linear-gradient(135deg,#cfc7bd,#5e6a78 60%,#2f3a47)}
.card-img.small-b{background:linear-gradient(135deg,#d8c3b0,#6a5a4c 55%,#2b2420)}
.feature-title{font-size:26px;font-weight:700;line-height:27px}
.card-title{font-size:15px;font-weight:500;line-height:19.5px;width:140px}
.card-text{font-size:8.6px;font-weight:300;line-height:13px;color:var(--muted);width:132px}
.short-rule{width:29px;height:2px;background:#111}
.divider{left:53px;top:702px;width:555px;height:1px;background:#eee}
.section-title{left:53px;top:742px;font-size:26px;font-weight:700}
.section-text{left:53px;top:792px;width:555px;font-size:6.4px;line-height:12.2px;color:#666}
.contact{left:36px;top:916px;width:641px;height:122px;background:var(--panel)}
.contact-title{left:60px;top:948px;font-size:12px;font-weight:700;font-style:italic}
.field{height:25px;border:1px solid var(--field-line);background:transparent;font-size:9px;color:#aaa;padding:6px 8px}
.contact .field,.contact-field{top:974px}
.submit{top:974px;left:560px;width:55px;height:25px;font-size:10px}
.social-bar{left:36px;top:1038px;width:641px;height:40px;display:flex}
.social-bar div{flex:1;display:flex;align-items:center;justify-content:center;color:#fff;font-size:9px;font-weight:500}
.footer{left:36px;top:1078px;width:641px;height:122px;background:var(--footer)}
.sub-title{left:258px;top:1107px;color:#fff;font-size:11px;font-weight:700;font-style:italic}
.dark-field{top:1128px;height:24px;border:1px solid #fff;font-size:9px;color:#888;padding:6px 8px}
.dark-sq{top:1128px;width:25px;height:25px;border:1px solid #fff;color:#fff;font-size:9px;display:flex;align-items:center;justify-content:center}
.copyright{left:61px;top:1167px;font-size:7px;color:#666}
</style>
</head>
<body>
<div class="abs sidebar"></div>
<div class="abs menu-icon"><span></span><span></span><span></span></div>

<div class="abs brand" style="left:61px;top:34px"><span class="brand-dot"></span><span class="brand-name">KARIM<br>DULVANE</span></div>
<div class="abs social-sq" style="left:562px;top:24px">C</div>
<div class="abs social-sq" style="left:592px;top:24px">P</div>

<div class="abs hero-panel" role="img" aria-label="Faded photo of a private jet with a young man standing on the tarmac"></div>
<div class="abs hero-video" role="img" aria-label="Video still of a young man holding a phone at a cafe table"></div>
<svg class="abs play" viewBox="0 0 44 44"><circle cx="22" cy="22" r="20.5" fill="none" stroke="#fff" stroke-width="2"/><path d="M18 14l11 8-11 8z" fill="#fff"/></svg>
<h1 class="abs hero-title">Karim<br>Dulvane</h1>
<div class="abs hero-rule"></div>
<p class="abs hero-sub">What You Will Learn On This<br>FREE Training:</p>
<div class="abs btn-red hero-btn">Show Me Exactly How You Did It</div>
<div class="abs arrow" style="left:35px;top:308px"><svg width="6" height="9" viewBox="0 0 6 9"><path d="M5 1L1.5 4.5 5 8" fill="none" stroke="#fff" stroke-width="1.2"/></svg></div>
<div class="abs arrow" style="left:639px;top:308px;width:38px"><svg width="6" height="9" viewBox="0 0 6 9"><path d="M1 1l3.5 3.5L1 8" fill="none" stroke="#fff" stroke-width="1.2"/></svg></div>

<div class="abs card-img" style="left:54px;top:401px;width:273px;height:190px" role="img" aria-label="Young man smiling with phone in hand at a cafe"></div>
<h2 class="abs feature-title" style="left:52px;top:607px">How You Can Drive<br>Laser Trageted Traffic</h2>

<div class="abs card-img small-a" style="left:342px;top:401px;width:130px;height:97px" role="img" aria-label="Two young men talking in a gallery"></div>
<h3 class="abs card-title" style="left:342px;top:514px">How you create a storvane store that converts</h3>
<p class="abs card-text" style="left:342px;top:581px">Building an eCommerce store is simple but building a store that actually makes people want to buy is more important!</p>
<div class="abs short-rule" style="left:342px;top:647px"></div>

<div class="abs card-img small-b" style="left:487px;top:401px;width:129px;height:97px" role="img" aria-label="Young man in a robe taking a mirror photo"></div>
<h3 class="abs card-title" style="left:487px;top:514px;width:145px">How you find hot &amp; trending products to cash out on</h3>
<p class="abs card-text" style="left:487px;top:581px">Most people try to sell things that they personally like and want to buy... The secret is to find hot trends and capitalize on...</p>
<div class="abs short-rule" style="left:487px;top:647px"></div>

<div class="abs divider"></div>
<h2 class="abs section-title">Free Training Reveals :</h2>
<p class="abs section-text">Building an eCommerce store is simple but building a store that actually makes people want to buy is more important!<br>HOW YOU FIND HOT &amp; TRENDING PRODUCTS TO CASH OUT ON Most people try to sell things that they personally like and want to buy... The secret is to find hot trends and capitalize on them while they're still hot! HOW YOU CAN DRIVE LASER TARGETED TRAFFIC After you build your store, add the hot and trending products the next step is to drive congruent traffic to generate sales!</p>
<div class="abs short-rule" style="left:53px;top:864px"></div>

<div class="abs contact"></div>
<h4 class="abs contact-title">WANT TO GET IN TOUCH WITH ME?</h4>
<div class="abs field contact-field" style="left:60px;width:110px">Name</div>
<div class="abs field contact-field" style="left:176px;width:116px">Email</div>
<div class="abs field contact-field" style="left:297px;width:126px">Subject</div>
<div class="abs field contact-field" style="left:429px;width:125px">Message</div>
<div class="abs btn-red submit">Submit</div>

<div class="abs social-bar">
  <div style="background:var(--pagebook)">Pagebook</div>
  <div style="background:var(--chirper)">Chirper</div>
  <div style="background:var(--circlely)">Circlely</div>
  <div style="background:var(--workline)">Workline</div>
  <div style="background:var(--pinboardy)">Pinboardy</div>
</div>

<div class="abs footer"></div>
<div class="abs brand footer" style="left:61px;top:1112px;background:none;width:auto;height:auto"><span class="brand-dot"></span><span class="brand-name">KARIM<br>DULVANE</span></div>
<h4 class="abs sub-title">SUBSCIBE</h4>
<div class="abs dark-field" style="left:258px;width:100px">Name</div>
<div class="abs dark-field" style="left:362px;width:110px">Email</div>
<div class="abs btn-red" style="left:475px;top:1128px;width:66px;height:24px;font-size:9.5px">Subscribe</div>
<div class="abs dark-sq" style="left:561px">C</div>
<div class="abs dark-sq" style="left:591px">P</div>
<p class="abs copyright">2017 © Copyright Karim Dulvane, All Rights Reserved.</p>
</body>
</html>
```